Stationery for a private security company, "Brenmoor Security Services Ltd."

Needed is a stationery design for a private security company. The designs must show professionalism and that our company mean nothing but business. Watermark of the company logo on the letterhead page is also a must. The final design must represent innovation and professionalism. It would be great if designers could integrate the colours black and silver onto the cards and letterheads..

Thank you

```html
<!DOCTYPE html>
<html lang="en">
<head>
<meta charset="utf-8">
<title>Brenmoor Security Services Ltd. — Stationery</title>
<link rel="stylesheet" href="https://fonts.googleapis.com/css2?family=Open+Sans:wght@400;600;700&display=swap">
<style>
:root{
  --bg:#ececec;
  --paper:#ffffff;
  --ink:#1a1a1a;
  --black:#050505;
  --silver:#b9b9bb;
  --text-grey:#555555;
  --accent:#2fa8d8;
  --sig:#d4d4d4;
}
*{margin:0;padding:0;box-sizing:border-box}
html,body{width:1200px;height:937px;overflow:hidden;background:var(--bg)}
body{position:relative;font-family:"Open Sans",Arial,sans-serif;color:var(--ink)}
.sheet{position:absolute;background:var(--paper);overflow:hidden}
.wordmark{font-weight:600;color:var(--ink);line-height:1.15;display:flex;align-items:center;gap:6px}
.wordmark .mark{background:var(--ink);flex:none}
.footer-band{position:absolute;left:0;right:0;bottom:0;background:var(--silver)}
.web-tab{position:absolute;right:0;background:var(--black);color:#fff;display:flex;align-items:center;justify-content:center;border-top-left-radius:12px}

/* letterhead */
.letterhead{left:184px;top:66px;width:389px;height:546px}
.letterhead .wordmark{position:absolute;left:36px;top:60px;width:120px;font-size:11px}
.letterhead .wordmark .mark{width:9px;height:9px}
.contact{position:absolute;left:264px;top:24px;font-size:7.5px;line-height:10.5px;color:var(--text-grey);list-style:none}
.contact li{display:flex;align-items:flex-start;gap:4px}
.contact li:first-child{font-weight:700;color:var(--ink);width:110px}
.contact svg{flex:none;margin-top:2px}
.letter{position:absolute;left:36px;top:140px;width:300px;font-size:5.4px;line-height:7.6px;color:var(--text-grey)}
.letter p{margin-bottom:9px}
.letter .date{margin-bottom:10px}
.letter .greeting{margin-bottom:3px;font-weight:700;color:var(--ink)}
.letter .body{margin-bottom:16px}
.signature{width:40px;height:22px;background:var(--sig);margin:6px 0 10px;border-radius:3px}
.letter .signer{font-weight:700;color:var(--ink);margin-bottom:0}
.letterhead .footer-band{height:22px}
.letterhead .web-tab{bottom:12px;width:180px;height:24px;font-size:11.5px}

/* continuation sheet */
.second{left:636px;top:40px;width:458px;height:576px}
.second .wordmark{position:absolute;left:184px;top:282px;width:110px;font-size:11px;justify-content:center;text-align:center}
.second .wordmark .mark{width:9px;height:9px}
.second .footer-band{height:28px}
.second .web-tab{bottom:15px;width:224px;height:26px;font-size:13px}

/* business cards */
.card{left:45px;width:177px;height:102px;border-radius:10px}
.card-front{top:655px}
.card-back{top:785px;height:100px}
.card-front .person{position:absolute;left:8px;top:17px;font-size:5.6px;line-height:7px}
.card-front .person strong{display:block;font-weight:700;color:var(--ink)}
.card-front .person span{color:var(--accent)}
.card-front .wordmark{position:absolute;left:114px;top:36px;width:58px;font-size:6.4px}
.card-front .wordmark .mark{width:5px;height:5px}
.card-front .contact{left:8px;top:58px;font-size:4.4px;line-height:5.8px}
.card-front .contact li:first-child{width:70px}
.card-front .web-tab{bottom:3px;width:82px;height:10px;font-size:4.8px;border-top-left-radius:6px;border-bottom-left-radius:6px}
.card-back .wordmark{position:absolute;left:52px;top:42px;width:80px;font-size:7.5px;justify-content:center}
.card-back .wordmark .mark{width:6px;height:6px}

/* envelopes */
.envelope-front{left:265px;top:671px;width:432px;height:210px}
.envelope-front .wordmark{position:absolute;left:20px;top:46px;width:130px;font-size:11px}
.envelope-front .wordmark .mark{width:9px;height:9px}
.envelope-front .footer-band{height:20px}
.envelope-front .web-tab{bottom:12px;width:210px;height:24px;font-size:12px}
.envelope-back{left:737px;top:671px;width:433px;height:208px}
.flap{position:absolute;left:0;top:0;width:100%;height:72px;background:var(--black);color:#fff;border-radius:0 0 34px 34px;display:flex;align-items:center;justify-content:center;font-size:18px}
.envelope-back .wordmark{position:absolute;left:155px;top:114px;width:124px;font-size:12px;justify-content:center;text-align:center}
.envelope-back .wordmark .mark{width:10px;height:10px}
</style>
</head>
<body>

<section class="sheet letterhead" aria-label="Letterhead">
  <div class="wordmark"><span class="mark"></span><span>Brenmoor Security Services Ltd.</span></div>
  <ul class="contact">
    <li><svg width="6" height="7" viewBox="0 0 6 7"><path d="M3 0a2.5 2.5 0 0 0-2.5 2.5C.5 4.4 3 7 3 7s2.5-2.6 2.5-4.5A2.5 2.5 0 0 0 3 0z" fill="#2fa8d8"/></svg>Floor 12, 40 Carden Row, Halford</li>
    <li><svg width="6" height="6" viewBox="0 0 6 6"><rect x="0.5" y="0.5" width="5" height="5" rx="1" fill="#2fa8d8"/></svg>021 555 0147</li>
    <li><svg width="6" height="6" viewBox="0 0 6 6"><path d="M0 6 3 0 6 6z" fill="#2fa8d8"/></svg>021 555 0148</li>
    <li><svg width="6" height="6" viewBox="0 0 6 6"><rect x="0" y="1.5" width="6" height="3" fill="#2fa8d8"/></svg>office@brenmoorsecurity.com</li>
  </ul>
  <div class="letter">
    <p class="date">July 2, 2012</p>
    <p class="greeting">Dear Sir,</p>
    <p>Harlow House, Quay St., Westland</p>
    <p class="body">Thank you for your recent enquiry about our site protection services. This letter sets out the scope of patrols, staffing levels and reporting we propose for your premises. All officers are licensed, vetted and trained to respond quickly to any incident.</p>
    <p class="body">Our control room monitors every assignment around the clock and keeps a full record of each shift.</p>
    <p class="body">We would welcome the chance to meet and review your requirements in person. Please find our service schedule enclosed, and do not hesitate to contact our office with any questions about terms, timing or the transition from your current provider.</p>
    <p>Best Regards,</p>
    <div class="signature" role="img" aria-label="Handwritten signature"></div>
    <p class="signer">Daniel Harte</p>
    <p style="margin-bottom:0">Director</p>
    <p>Harlow House, Quay St., Westland</p>
  </div>
  <div class="footer-band"></div>
  <div class="web-tab">www.brenmoorsecurity.com</div>
</section>

<section class="sheet second" aria-label="Continuation sheet">
  <div class="wordmark"><span class="mark"></span><span>Brenmoor Security Services Ltd.</span></div>
  <div class="footer-band"></div>
  <div class="web-tab">www.brenmoorsecurity.com</div>
</section>

<section class="sheet card card-front" aria-label="Business card front">
  <div class="person"><strong>OWEN MERCER</strong><span>Managing Director</span></div>
  <div class="wordmark"><span class="mark"></span><span>Brenmoor Security Services Ltd.</span></div>
  <ul class="contact">
    <li>Floor 12, 40 Carden Row, Halford</li>
    <li>021 555 0147</li>
    <li>021 555 0148</li>
    <li>office@brenmoorsecurity.com</li>
  </ul>
  <div class="web-tab">www.brenmoorsecurity.com</div>
</section>

<section class="sheet card card-back" aria-label="Business card back">
  <div class="wordmark"><span class="mark"></span><span>Brenmoor Security Services Ltd.</span></div>
</section>

<section class="sheet envelope-front" aria-label="Envelope front">
  <div class="wordmark"><span class="mark"></span><span>Brenmoor Security Services Ltd.</span></div>
  <div class="footer-band"></div>
  <div class="web-tab">www.brenmoorsecurity.com</div>
</section>

<section class="sheet envelope-back" aria-label="Envelope back">
  <div class="flap">www.brenmoorsecurity.com</div>
  <div class="wordmark"><span class="mark"></span><span>Brenmoor Security Services Ltd.</span></div>
</section>

</body>
</html>
```